Brell Stone Company Business Cards

Front and Back Business Card - logo and text setup - cool design. I need workable photoshop or illustrator files so I can setup each employee card with design that is created
Updates

Hi everyone, thank you for the great entries. Please no more white and blue cards - there are so many already - black and silver only now please. thanks!

Target Market(s)

Construction Industry - Facility Managers

Industry/Entity Type

Construction

Contact Information for Business Card

I really like contemporary simplistic looks - clean neat....not opposed to seeing some black backrounds

Requirements
Must have
• Logo/website address with design on front only - www.brellstone-example.com (logo attached)
• Back:
• Name/Title/Company Address/Phone/email address
Nice to have
• Cool design
Should not have
• Nothing gimmicky like Fire or Water - since we are a Fire Protection company - it has all been done

```html
<!DOCTYPE html>
<html lang="en">
<head>
<meta charset="utf-8">
<title>Brell Stone Company Business Cards</title>
<link href="https://fonts.googleapis.com/css2?family=Lato:wght@400;700;900&display=swap" rel="stylesheet">
<style>
  :root {
    --page: #ffffff;
    --card: #0f1113;
    --silver-bright: #e4e7ea;
    --silver: #c3c8cd;
    --silver-muted: #9ba1a7;
  }
  * { margin: 0; padding: 0; box-sizing: border-box; }
  html, body { width: 1200px; height: 1200px; overflow: hidden; background: var(--page); }
  body { position: relative; font-family: "Lato", sans-serif; }

  .card {
    position: absolute;
    left: 150px;
    width: 900px;
    height: 540px;
    background: var(--card);
    overflow: hidden;
  }
  .card-front { top: 56px; }
  .card-back { top: 612px; }

  .wordmark {
    position: absolute;
    display: flex;
    align-items: center;
    gap: 14px;
    font-weight: 900;
    color: var(--silver);
    white-space: nowrap;
    letter-spacing: -0.5px;
  }
  .wordmark-mark { width: 22px; height: 22px; background: var(--silver-muted); }
  .card-front .wordmark { left: 50%; top: 270px; transform: translate(-50%, -50%); font-size: 64px; }
  .card-back .wordmark { left: 74px; top: 136px; transform: translateY(-50%); font-size: 58px; }

  .rule { position: absolute; height: 3px; background: var(--silver-muted); }
  .rule-left { left: 0; top: 469px; width: 280px; }
  .rule-right { right: 0; top: 469px; width: 280px; }
  .website {
    position: absolute;
    left: 50%;
    top: 470px;
    transform: translate(-50%, -50%);
    color: var(--silver);
    font-size: 17px;
    font-weight: 700;
    letter-spacing: 4px;
    white-space: nowrap;
  }

  .person { position: absolute; left: 568px; top: 270px; }
  .person-name { color: var(--silver-bright); font-size: 39px; font-weight: 700; line-height: 1; }
  .person-title { color: var(--silver-muted); font-size: 26px; font-weight: 400; margin-top: 6px; line-height: 1; }
  .rule-divider { left: 0; top: 354px; width: 661px; }

  .address {
    position: absolute;
    left: 72px;
    top: 408px;
    display: flex;
    gap: 10px;
    color: var(--silver);
    font-size: 22px;
    line-height: 27px;
  }
  .address svg { flex: none; margin-top: 1px; }

  .contact-list {
    position: absolute;
    right: 86px;
    top: 384px;
    list-style: none;
    color: var(--silver);
    font-size: 22px;
  }
  .contact-list li {
    display: flex;
    justify-content: flex-end;
    align-items: center;
    gap: 10px;
    height: 30px;
    margin-bottom: 13px;
  }
  .icon { fill: var(--silver-bright); flex: none; }
</style>
</head>
<body>

<section class="card card-front" aria-label="Business card front">
  <div class="wordmark"><span class="wordmark-mark"></span>Brell Stone</div>
  <div class="rule rule-left"></div>
  <div class="website">www.brellstone-example.com</div>
  <div class="rule rule-right"></div>
</section>

<section class="card card-back" aria-label="Business card back">
  <div class="wordmark"><span class="wordmark-mark"></span>Brell Stone</div>

  <div class="person">
    <p class="person-name">Dana Wexford</p>
    <p class="person-title">Founder</p>
  </div>
  <div class="rule rule-divider"></div>

  <div class="address">
    <svg class="icon" width="18" height="26" viewBox="0 0 18 26" aria-hidden="true">
      <path d="M9 0C4 0 0 4 0 9c0 6.5 9 17 9 17s9-10.5 9-17C18 4 14 0 9 0zm0 13a4 4 0 1 1 0-8 4 4 0 0 1 0 8z"/>
    </svg>
    <p>48 Harrow Lane<br>Marlow, ST 10482</p>
  </div>

  <ul class="contact-list">
    <li>000-000-000
      <svg class="icon" width="24" height="24" viewBox="0 0 24 24" aria-hidden="true">
        <path d="M6.6 10.8a15.5 15.5 0 0 0 6.6 6.6l2.2-2.2c.3-.3.7-.4 1-.2 1.1.4 2.3.6 3.6.6.6 0 1 .4 1 1V20c0 .6-.4 1-1 1A17 17 0 0 1 3 4c0-.6.4-1 1-1h3.5c.6 0 1 .4 1 1 0 1.3.2 2.5.6 3.6.1.3 0 .7-.2 1z"/>
      </svg>
    </li>
    <li>info@yourmail.com
      <svg class="icon" width="28" height="22" viewBox="0 0 28 22" aria-hidden="true">
        <path d="M0 2a2 2 0 0 1 2-2h24a2 2 0 0 1 2 2v1L14 12 0 3z"/>
        <path d="M0 6l14 9 14-9v14a2 2 0 0 1-2 2H2a2 2 0 0 1-2-2z"/>
      </svg>
    </li>
  </ul>
</section>

</body>
</html>
```